BrindleStaffing Business Card Design

We are a staffing company finding positions for dedicated nurses and physicians.

Target Market(s)

Business Professionals

Industry/Entity Type

Staffing

Contact Information for Business Card

Gordon Pratley
Chairman
417 39th Avenue South
SAINT PETERSBURG FL 33712
813-555-4172 Mobile
813-555-8036 Fax
gpratley@brindlestaffing.com
www.brindlestaffing.com

Font styles to use
Sans Serif

Colors
fbee3e
f04a50
f37122

Requirements
Must have
• Logo Attached, see colors below. We'd like to see Yellow, Orange and Red.

```html
<!DOCTYPE html>
<html lang="en">
<head>
<meta charset="utf-8">
<title>BrindleStaffing Business Card</title>
<link rel="stylesheet" href="https://fonts.googleapis.com/css2?family=Lexend:wght@400;500;600&display=swap">
<style>
  :root {
    --yellow: #f4ef3f;
    --red: #f04a50;
    --orange: #f37122;
    --ink: #1f1f1f;
    --muted: #8a8a8a;
    --paper: #ffffff;
    --stage: #ffffff;
  }
  * { margin: 0; padding: 0; box-sizing: border-box; }
  html, body {
    width: 1200px; height: 1200px; overflow: hidden;
    background: var(--stage);
    font-family: "Lexend", Arial, sans-serif;
  }
  .canvas { position: relative; width: 1200px; height: 1200px; }
  .card {
    position: absolute; left: 240px; width: 720px; height: 420px;
    border-radius: 26px; overflow: hidden;
    box-shadow: 0 14px 28px rgba(0,0,0,0.16);
  }
  .card-front { top: 142px; background: var(--yellow); }
  .card-back { top: 638px; background: var(--paper); }

  .wordmark {
    position: absolute; left: 0; right: 0; text-align: center;
    color: var(--red); font-weight: 600; letter-spacing: -0.5px; line-height: 1;
  }
  .card-front .wordmark { top: 188px; font-size: 58px; }
  .card-back .wordmark { top: 82px; font-size: 45px; }

  .identity {
    position: absolute; right: 384px; top: 224px; width: 320px; height: 64px;
  }
  .identity .name {
    position: absolute; right: 0; top: 0; white-space: nowrap;
    font-size: 32px; font-weight: 500; color: var(--red); line-height: 1;
  }
  .identity .role {
    position: absolute; right: 0; top: 44px; white-space: nowrap;
    font-size: 16px; color: var(--ink); line-height: 1;
  }
  .divider {
    position: absolute; left: 352px; top: 190px; width: 1.5px; height: 126px;
    background: linear-gradient(to bottom, transparent, var(--muted) 20%, var(--muted) 80%, transparent);
  }
  .contacts { position: absolute; left: 373px; top: 208px; list-style: none; }
  .contacts li {
    display: flex; align-items: center; height: 25px;
    font-size: 17px; color: var(--ink); white-space: nowrap;
  }
  .contacts svg { width: 14px; height: 14px; margin-right: 11px; fill: var(--orange); flex: none; }

  .address-band {
    position: absolute; left: 0; right: 0; top: 365px; height: 27px;
    background: var(--yellow);
    display: flex; align-items: center; justify-content: center;
    font-size: 16px; font-weight: 500; color: var(--ink); letter-spacing: 0.2px;
  }
</style>
</head>
<body>
<main class="canvas">

  <section class="card card-front">
    <div class="wordmark">BrindleStaffing</div>
  </section>

  <section class="card card-back">
    <div class="wordmark">BrindleStaffing</div>

    <div class="identity">
      <div class="name">Gordon Pratley</div>
      <div class="role">Founder &amp; CEO</div>
    </div>

    <div class="divider"></div>

    <ul class="contacts">
      <li>
        <svg viewBox="0 0 16 16" aria-hidden="true"><path d="M3.5 1.5l2.4 0 1 3.2-1.6 1.2a8 8 0 0 0 4.8 4.8l1.2-1.6 3.2 1v2.4c0 .8-.7 1.5-1.5 1.5C7 14 2 9 2 3c0-.8.7-1.5 1.5-1.5z"/></svg>
        813-555-4172
      </li>
      <li>
        <svg viewBox="0 0 16 16" aria-hidden="true"><path d="M4 1h8v4H4zM2 6h12a1 1 0 0 1 1 1v5h-3v3H4v-3H1V7a1 1 0 0 1 1-1zm3 5v3h6v-3z"/></svg>
        813-555-8036
      </li>
      <li>
        <svg viewBox="0 0 16 16" aria-hidden="true"><path d="M1 3h14v1.2L8 9 1 4.2zM1 5.8l7 4.8 7-4.8V13H1z"/></svg>
        gpratley@brindlestaffing.com
      </li>
      <li>
        <svg viewBox="0 0 16 16" aria-hidden="true"><path d="M8 1a7 7 0 1 0 0 14A7 7 0 0 0 8 1zm0 1.4c.8 0 1.7 1.5 2 3.8H6c.3-2.3 1.2-3.8 2-3.8zM4.6 6.2H2.7a5.6 5.6 0 0 1 3-3.4 9 9 0 0 0-1.1 3.4zm0 1.4c0 1.4.3 2.7.8 3.6a5.6 5.6 0 0 1-2.9-3.6zm1.4 0h4c-.1 2.4-1 4-2 4s-1.9-1.6-2-4zm5.4 0h2.1a5.6 5.6 0 0 1-2.9 3.6c.5-.9.8-2.2.8-3.6zm0-1.4a9 9 0 0 0-1.1-3.4 5.6 5.6 0 0 1 3 3.4z"/></svg>
        www.brindlestaffing.com
      </li>
    </ul>

    <div class="address-band">417 39th Avenue South, SAINT PETERSBURG FL 33712</div>
  </section>

</main>
</body>
</html>
```